Dancing Emoji Lady but make it silhouette

We need a main image for the front of a hard wine seltzer. The best emoji that would describe this brand is the dancing lady in red dress emoji. We want to re-create the essence of this emoji in a silhouette (like an outline) so it's our own design, but it captures the fun and flirtatiousness of that emoji. We have three flavors - peach (peach color), fruit punch (red/purple color), and citrus (orange color) - so the only color should be the outline of her swooshing dress.

I'm attaching an image of the emoji I wish to emulate, and then some examples of what I mean by "silhouette" - I know the attached examples are not of a woman dancing, but it's the line/style that I want to emulate here to make a silhouette of the dancer emoji.

```html
<!DOCTYPE html>
<html lang="en">
<head>
<meta charset="utf-8">
<title>Calora Peach Bellini – Can Label</title>
<link rel="stylesheet" href="https://fonts.googleapis.com/css2?family=Fraunces:opsz,wght@9..144,600;9..144,800&family=Oswald:wght@500&family=Bebas+Neue&display=swap">
<style>
  :root {
    --page: #eaeaea;
    --peach: #f8a592;
    --brown: #6b1e0c;
    --white: #ffffff;
    --dress-red: #a51c17;
    --art-light: #f7b4a3;
  }
  * { margin: 0; padding: 0; box-sizing: border-box; }
  html, body { width: 1200px; height: 738px; overflow: hidden; }
  body { background: var(--page); position: relative; }

  .label {
    position: absolute;
    left: 401px; top: 49px;
    width: 398px; height: 640px;
    background: var(--peach);
    color: var(--brown);
    text-align: center;
  }
  .brand-mark {
    position: absolute; left: 0; right: 0; top: 44px;
    display: flex; flex-direction: column; align-items: center; gap: 6px;
  }
  .brand-dot {
    width: 16px; height: 16px; border-radius: 50%;
    background: var(--white);
  }
  .brand-name {
    font-family: "Fraunces", Georgia, serif;
    font-weight: 800;
    font-size: 54px;
    line-height: 1;
    letter-spacing: -0.5px;
    color: var(--brown);
  }
  .dancer-art {
    position: absolute;
    left: 103px; top: 184px;
    width: 177px; height: 245px;
    background: radial-gradient(ellipse at 55% 35%, var(--dress-red) 0%, #c9584a 28%, var(--art-light) 75%);
    border-radius: 40% 40% 30% 30%;
    opacity: 0.55;
  }
  .flavour {
    position: absolute; left: 0; right: 0; top: 438px;
    font-family: "Bebas Neue", "Oswald", sans-serif;
    font-size: 38px; line-height: 1;
    letter-spacing: 0.5px;
    color: var(--white);
  }
  .product-type {
    position: absolute; left: 0; right: 0; top: 477px;
    font-family: "Fraunces", Georgia, serif;
    font-weight: 600;
    font-size: 16px;
    color: var(--brown);
  }
  .claims {
    position: absolute; left: 0; right: 0; top: 508px;
    height: 38px;
  }
  .claim-seal { position: absolute; top: 0; width: 38px; height: 38px; }
  .claim-seal--calories { left: 111px; }
  .claim-seal--sugar { left: 249px; }
  .claim-seal text {
    font-family: "Oswald", sans-serif; font-weight: 500;
    font-size: 6.4px; letter-spacing: 0.4px; fill: var(--brown);
  }
  .claim-organic {
    position: absolute; left: 0; right: 0; top: 4px;
    font-family: "Oswald", sans-serif; font-weight: 500;
    font-size: 10.5px; line-height: 15px;
    letter-spacing: 0.3px;
  }
  .volume {
    position: absolute; left: 0; right: 0; top: 556px;
    font-family: "Oswald", sans-serif; font-weight: 500;
    font-size: 10px; letter-spacing: 0.3px;
  }
  .volume .divider { margin: 0 4px; }
</style>
</head>
<body>
  <main class="label">
    <div class="brand-mark">
      <span class="brand-dot"></span>
      <span class="brand-name">Calora</span>
    </div>

    <div class="dancer-art" role="img" aria-label="Line illustration of a woman dancing in a swirling red dress, holding a glass of wine"></div>

    <h1 class="flavour">PEACH BELLINI</h1>
    <p class="product-type">Hard Wine Seltzer</p>

    <div class="claims">
      <svg class="claim-seal claim-seal--calories" viewBox="0 0 38 38" aria-label="Only 120 calories">
        <defs><path id="seal-path-a" d="M19,19 m-13,0 a13,13 0 1,1 26,0 a13,13 0 1,1 -26,0"/></defs>
        <circle cx="19" cy="19" r="18" fill="none" stroke="var(--brown)" stroke-width="1"/>
        <text><textPath href="#seal-path-a">ONLY 120 · CALORIES ·</textPath></text>
      </svg>
      <p class="claim-organic">MADE WITH<br>ORGANIC GRAPES</p>
      <svg class="claim-seal claim-seal--sugar" viewBox="0 0 38 38" aria-label="No added sugar">
        <defs><path id="seal-path-b" d="M19,19 m-13,0 a13,13 0 1,1 26,0 a13,13 0 1,1 -26,0"/></defs>
        <circle cx="19" cy="19" r="18" fill="none" stroke="var(--brown)" stroke-width="1"/>
        <text><textPath href="#seal-path-b">NO ADDED · SUGAR ·</textPath></text>
      </svg>
    </div>

    <p class="volume">6% ABV<span class="divider">|</span>250 mL</p>
  </main>
</body>
</html>
```